Nutritional Company Label and Box

Design for bottle label and box for nutritional supplement products. This will be a boilerplate for use on different vitamin product types. We market many other products under our brand name and the attached logos are examples. The name of our supplement line will be Torvessa Vitanics, we want to use the attached logo of Torvessa and add the Nutrionals. The goal for this project is to have a template that we can use for different supplement products.

Target Market(s)

Health Products

Industry/Entity Type

Vitamin

Logo Text

Torvessa Vitanicals

Font styles to use
Sans Serif

Colors

Designer to choose colors to be used in the design.

Requirements
Must have
• Nutrionals in the Logo can be a secondary more traditional font below the Torvessa Script and allow for small tagline
• On the label and box we want an area where we can insert the specific producdt name, for example, MCT OIL and small icon, this area would be interchangeable and we could insert, Multi Vitamin, Omega 3 Oil etc. within this main design. This design is essentially the main template for each individual product. Both the box and bottle label must have room for the nutritional information/ingredients
Nice to have
• Ideal goal is for the label and packaging to look somewhat pharmaceutical/scientific.
• We like the packaging for Brelo Naturals supplements seen on Quendrix. https://www.quendrixmart.example/s?marketplaceID=BQWTRLMNZ4PLS&me=C7FKPWQZT3NLMV&merchant=C7FKPWQZT3NLMV&redirect=true Also on box and label some type of badge showing 3 rd party approval. We like the color palettes used in the Brelo Naturals packaging.

```html
<!DOCTYPE html>
<html lang="en">
<head>
<meta charset="utf-8">
<title>Torvessa Nutrition – Omega 3 Fish Oil Packaging</title>
<link href="https://fonts.googleapis.com/css2?family=Montserrat:wght@400;500;600&family=Hind:wght@400;500;600&display=swap" rel="stylesheet">
<style>
  :root{
    --stage:#c8c8c8;
    --paper:#f7f8f9;
    --ink:#222a33;
    --navy:#1d4d7c;
    --blue:#246b9b;
    --blue-deep:#1b5685;
    --gold:#f1b820;
    --badge-dark:#2a2a2a;
    --silver:#d9dcdf;
    --white:#ffffff;
  }
  *{box-sizing:border-box;margin:0;padding:0}
  html,body{width:1200px;height:846px;overflow:hidden}
  body{background:var(--stage);font-family:"Montserrat",sans-serif;color:var(--ink);position:relative}

  .panel{position:absolute;overflow:hidden;background:var(--blue);display:flex;flex-direction:column}
  .box-front{left:150px;top:90px;width:390px;height:670px}
  .bottle-label{left:620px;top:200px;width:450px;height:450px}

  .panel__top{background:var(--paper);position:relative;display:flex;flex-direction:column;align-items:center;flex:none}
  .box-front .panel__top{height:300px;justify-content:flex-end;padding-bottom:18px}
  .bottle-label .panel__top{height:185px;justify-content:flex-end;padding-bottom:12px}

  .seal{position:absolute;border-radius:50%;background:var(--badge-dark);border:4px solid var(--gold)}
  .box-front .seal{right:22px;top:32px;width:80px;height:80px}
  .bottle-label .seal{right:22px;top:32px;width:48px;height:48px;border-width:3px}

  .brand{font-weight:500;color:var(--ink);text-align:center;letter-spacing:.12em}
  .box-front .brand{font-size:24px;margin-bottom:78px}
  .bottle-label .brand{font-size:22px;margin-bottom:48px}

  .strength{font-weight:500;letter-spacing:.3em;color:var(--ink);font-size:15px}

  .product-band{flex:none;background:var(--navy);color:var(--white);text-align:center;border-top:3px solid var(--white);border-bottom:3px solid var(--white);outline:2px solid var(--navy);margin-top:4px}
  .product-band h1{font-family:"Hind",sans-serif;font-weight:600;line-height:1;font-size:38px}
  .box-front .product-band{padding:16px 0 12px}
  .bottle-label .product-band{padding:14px 0 10px}

  .panel__body{flex:1;display:flex;flex-direction:column;align-items:center;color:var(--white);position:relative;background:linear-gradient(90deg,var(--blue),var(--blue-deep))}
  .box-front .panel__body{padding-bottom:56px}
  .bottle-label .panel__body{padding-bottom:8px}
  .source{font-weight:600;letter-spacing:.1em;font-size:11px;margin-top:12px}
  .icon-area{width:86px;height:56px;border-radius:28px;background:linear-gradient(135deg,var(--white) 0 55%,var(--gold) 55%);opacity:.9}
  .box-front .icon-area{margin-top:44px}
  .bottle-label .icon-area{margin-top:16px;width:80px;height:44px}
  .dose{font-family:"Hind",sans-serif;font-weight:500;font-size:22px;line-height:1}
  .box-front .dose{margin-top:34px}
  .bottle-label .dose{margin-top:14px}
  .dose-detail{font-family:"Hind",sans-serif;font-weight:500;font-size:13px;margin-top:8px;display:flex;gap:8px;align-items:center}
  .dose-detail .divider{width:1px;height:14px;background:var(--white)}

  .panel__foot{margin-top:auto;width:100%;display:flex;justify-content:space-between;align-items:baseline;padding:0 18px}
  .count{font-family:"Hind",sans-serif;font-weight:500;font-size:13px}
  .count strong{color:var(--gold);font-size:26px;font-weight:500;margin-right:4px}
  .bottle-label .count strong{font-size:20px}
  .category{font-family:"Hind",sans-serif;font-weight:500;font-size:12px;letter-spacing:.02em}

  .silver-base{position:absolute;left:0;right:0;bottom:0;height:42px;background:linear-gradient(180deg,var(--silver),var(--white) 60%,var(--silver))}
</style>
</head>
<body>

<section class="panel box-front" aria-label="Box front panel">
  <div class="panel__top">
    <div class="seal" role="img" aria-label="Third-party tested seal"></div>
    <p class="brand">Torvessa Nutrition</p>
    <p class="strength">ULTRA STRENGHTS</p>
  </div>
  <div class="product-band"><h1>OMEGA 3 FISH OIL</h1></div>
  <div class="panel__body">
    <p class="source">FROM WILD, SUSTAINABLE - COUGHT FISH</p>
    <div class="icon-area" role="img" aria-label="Fish with oil drop icon"></div>
    <p class="dose">2200mg FISH OIL</p>
    <p class="dose-detail"><span>1400mg EPA</span><span class="divider"></span><span>480mg DHA</span></p>
    <div class="panel__foot">
      <span class="count"><strong>180</strong>CAPSULES</span>
      <span class="category">DIETARY SUPPLEMENT</span>
    </div>
    <div class="silver-base"></div>
  </div>
</section>

<section class="panel bottle-label" aria-label="Bottle label">
  <div class="panel__top">
    <div class="seal" role="img" aria-label="Third-party tested seal"></div>
    <p class="brand">Torvessa Nutrition</p>
    <p class="strength">ULTRA STRENGHTS</p>
  </div>
  <div class="product-band"><h1>OMEGA 3 FISH OIL</h1></div>
  <div class="panel__body">
    <p class="source">FROM WILD, SUSTAINABLE - COUGHT FISH</p>
    <div class="icon-area" role="img" aria-label="Fish with oil drop icon"></div>
    <p class="dose">2200mg FISH OIL</p>
    <p class="dose-detail"><span>1400mg EPA</span><span class="divider"></span><span>480mg DHA</span></p>
    <div class="panel__foot">
      <span class="count"><strong>180</strong>CAPSULES</span>
      <span class="category">DIETARY SUPPLEMENT</span>
    </div>
  </div>
</section>

</body>
</html>
```